Corvane Card

The logo is the Spanish flag colors I want a vibrant eye catching design with the yellow / red colors over either Navy or white background or black even ,
Would like a 2D feel to the logo with another lighter color logo under it look ,

Contact Information for Business Card

Corvane Flooring
Teodor Vashkin
Main Number
Cell Number
Fax Number

Website on the side of the card somewhere

Font styles to use
Sans Serif

Colors
ec1f27
ffc214

Requirements
Must have
• 2 logos feel one is bolder and the other one underneath very light

```html
<!DOCTYPE html>
<html lang="en">
<head>
<meta charset="utf-8">
<title>Corvane Flooring – Business Card</title>
<link href="https://fonts.googleapis.com/css2?family=Archivo+Black&family=Montserrat:wght@500&display=swap" rel="stylesheet">
<style>
  :root {
    --red: #ec1f27;
    --yellow: #ffc214;
    --card: #0d0d0d;
    --bg: #2b2b2b;
    --ink: #ffffff;
    --emboss: #262626;
    --rule: #3a3a3a;
  }
  * { margin: 0; padding: 0; box-sizing: border-box; }
  html, body { width: 1200px; height: 1040px; overflow: hidden; }
  body {
    background: var(--bg);
    display: flex;
    flex-direction: column;
    align-items: center;
    justify-content: center;
    gap: 60px;
    font-family: "Montserrat", sans-serif;
  }
  .card {
    width: 700px;
    height: 400px;
    background: var(--card);
    position: relative;
    box-shadow: 0 14px 30px rgba(0,0,0,.55);
  }
  .card--back { border-radius: 110px 0 110px 0; display: flex; align-items: center; justify-content: center; }
  .card--front { border-radius: 0 110px 0 110px; display: flex; }

  .wordmark {
    font-family: "Archivo Black", sans-serif;
    line-height: 1.05;
    letter-spacing: 2px;
  }
  .wordmark--faint { color: var(--emboss); font-size: 44px; text-align: left; }
  .wordmark--faint .wordmark__line2 { display: block; letter-spacing: 18px; font-size: 26px; }

  .brand-side {
    width: 330px;
    display: flex;
    align-items: center;
    justify-content: center;
    border-right: 1px solid var(--rule);
    margin: 60px 0;
  }
  .wordmark--bold { color: var(--red); font-size: 40px; }
  .wordmark--bold .wordmark__line2 { display: block; letter-spacing: 14px; font-size: 24px; }
  .brand-mark {
    width: 26px; height: 26px; background: var(--red);
    border-radius: 4px; margin-bottom: 14px;
  }

  .contact-side {
    flex: 1;
    padding: 110px 30px 0 40px;
  }
  .person-name {
    font-family: "Archivo Black", sans-serif;
    font-size: 28px;
    letter-spacing: 2px;
    margin-bottom: 22px;
    white-space: nowrap;
  }
  .person-name__first { color: var(--red); }
  .person-name__last { color: var(--yellow); }
  .contact-list { list-style: none; }
  .contact-list li {
    display: flex; align-items: center; gap: 12px;
    color: var(--ink); font-size: 18px; margin-bottom: 6px;
  }
  .contact-list svg { width: 18px; height: 18px; flex: none; }
  .accent { color: var(--red); }
</style>
</head>
<body>

<section class="card card--back" aria-label="Card back">
  <div class="wordmark wordmark--faint">
    CORVANE<span class="wordmark__line2">FLOORING</span>
  </div>
</section>

<section class="card card--front" aria-label="Card front">
  <div class="brand-side">
    <div>
      <div class="brand-mark"></div>
      <div class="wordmark wordmark--bold">
        CORVANE<span class="wordmark__line2">FLOORING</span>
      </div>
    </div>
  </div>
  <div class="contact-side">
    <h1 class="person-name"><span class="person-name__first">TEODOR</span> <span class="person-name__last">VASHKIN</span></h1>
    <ul class="contact-list">
      <li>
        <svg viewBox="0 0 24 24" fill="#ec1f27" aria-hidden="true"><path d="M3 9c0-3 4-5 9-5s9 2 9 5v2h-5V9H8v2H3z"/><rect x="6" y="12" width="12" height="8" rx="2"/></svg>
        312 640 2187
      </li>
      <li>
        <svg viewBox="0 0 24 24" fill="none" stroke="#ec1f27" stroke-width="2.5" aria-hidden="true"><rect x="6" y="2" width="12" height="20" rx="2"/><line x1="10" y1="18" x2="14" y2="18"/></svg>
        312 640 5591
      </li>
      <li>
        <svg viewBox="0 0 24 24" fill="#ec1f27" aria-hidden="true"><rect x="7" y="2" width="10" height="6"/><rect x="2" y="8" width="20" height="9" rx="2"/><rect x="7" y="14" width="10" height="8" fill="#0d0d0d" stroke="#ec1f27" stroke-width="2"/></svg>
        312 640 7730
      </li>
      <li>
        <svg viewBox="0 0 24 24" fill="none" stroke="#ec1f27" stroke-width="2.5" aria-hidden="true"><rect x="2" y="5" width="20" height="14"/><polyline points="2,5 12,13 22,5"/></svg>
        hello@corvanemail.com
      </li>
      <li>
        <svg viewBox="0 0 24 24" fill="none" stroke="#ec1f27" stroke-width="2.5" aria-hidden="true"><circle cx="12" cy="12" r="10"/><ellipse cx="12" cy="12" rx="4" ry="10"/><line x1="2" y1="12" x2="22" y2="12"/></svg>
        <span>www.<span class="accent">corvanefloors</span>.com</span>
      </li>
    </ul>
  </div>
</section>

</body>
</html>
```